Im open to ideas.. I was thinking on my business cards aswell as my logo. a place for my name. email. phone number and abn..

ive attched a file with my business logo. which i dont love the colours.. i was think a dark background with charcoal letters so something along those colour schumes but im open to ideas..

BRM Constructions

```html
<!DOCTYPE html>
<html lang="en">
<head>
<meta charset="utf-8">
<title>BRM Constructions – Business Card</title>
<link href="https://fonts.googleapis.com/css2?family=Montserrat:wght@400;500;700&display=swap" rel="stylesheet">
<style>
  :root {
    --page-bg: #e4e5e7;
    --card-bg: #000000;
    --brand-red: #e5202a;
    --text-white: #ffffff;
    --rule-light: #d9d9d9;
  }
  * { margin: 0; padding: 0; box-sizing: border-box; }
  html, body {
    width: 1200px;
    height: 921px;
    overflow: hidden;
    background: var(--page-bg);
    font-family: "Montserrat", Arial, sans-serif;
  }
  .business-card {
    position: absolute;
    left: 370px;
    top: 58px;
    width: 460px;
    height: 804px;
    background: var(--card-bg);
    border-radius: 34px;
    color: var(--text-white);
    text-align: center;
  }
  .brand-name {
    position: absolute;
    top: 148px;
    left: 0;
    right: 0;
    font-weight: 700;
    color: var(--text-white);
    line-height: 1.05;
  }
  .brand-name .brand-main {
    display: block;
    font-size: 78px;
    letter-spacing: 2px;
  }
  .brand-name .brand-sub {
    display: block;
    font-size: 16px;
    letter-spacing: 12px;
    margin-top: 8px;
    padding-left: 12px;
  }
  .divider {
    position: absolute;
    left: 98px;
    width: 264px;
    height: 3px;
    background: linear-gradient(to right, transparent, var(--rule-light) 25%, var(--text-white) 50%, var(--rule-light) 75%, transparent);
  }
  .divider--top { top: 498px; }
  .divider--bottom { top: 747px; }
  .contact-line {
    position: absolute;
    left: 0;
    right: 0;
    font-size: 19px;
    font-weight: 400;
    letter-spacing: 0.3px;
    line-height: 1;
  }
  .person-name {
    top: 522px;
    font-size: 29px;
    font-weight: 500;
    color: var(--brand-red);
    letter-spacing: 0.5px;
  }
  .person-role { top: 557px; }
  .abn { top: 586px; }
  .abn .abn-label { color: var(--brand-red); }
  .contact-icons {
    position: absolute;
    top: 625px;
    left: 0;
    right: 0;
    display: flex;
    justify-content: center;
    gap: 8px;
  }
  .contact-icons svg { width: 15px; height: 15px; }
  .phone { top: 661px; }
  .email { top: 686px; }
  .website { top: 710px; }
</style>
</head>
<body>
  <div class="business-card">
    <div class="brand-name">
      <span class="brand-main">BRM</span>
      <span class="brand-sub">CONSTRUCTIONS</span>
    </div>

    <div class="divider divider--top"></div>

    <p class="contact-line person-name">MARCUS HALE</p>
    <p class="contact-line person-role">Director</p>
    <p class="contact-line abn"><span class="abn-label">ABN</span>: 41 286 503 117</p>

    <div class="contact-icons">
      <svg viewBox="0 0 16 16" aria-label="Phone">
        <path d="M4 1.5 L6 4.5 L4.8 6 C5.6 8 7.5 10 10 11.2 L11.5 10 L14.5 12 L13 14.5 C7.5 14 2 8.5 1.5 3 Z" fill="none" stroke="var(--brand-red)" stroke-width="1.4" stroke-linejoin="round"/>
      </svg>
      <svg viewBox="0 0 16 16" aria-label="Email">
        <rect x="1.5" y="3.5" width="13" height="9" fill="none" stroke="var(--brand-red)" stroke-width="1.4"/>
        <path d="M1.5 3.5 L8 9 L14.5 3.5" fill="none" stroke="var(--brand-red)" stroke-width="1.4"/>
      </svg>
      <svg viewBox="0 0 16 16" aria-label="Website">
        <circle cx="8" cy="8" r="6.5" fill="none" stroke="var(--brand-red)" stroke-width="1.3"/>
        <ellipse cx="8" cy="8" rx="3" ry="6.5" fill="none" stroke="var(--brand-red)" stroke-width="1.1"/>
        <path d="M1.5 8 H14.5 M2.5 4.8 H13.5 M2.5 11.2 H13.5" stroke="var(--brand-red)" stroke-width="1.1"/>
      </svg>
    </div>

    <p class="contact-line phone">+330 2460-1284</p>
    <p class="contact-line email">info@brmconstructions.com</p>
    <p class="contact-line website">www.brmconstructions.com</p>

    <div class="divider divider--bottom"></div>
  </div>
</body>
</html>
```